Wellness Coach/Personal trainer needs wordpress site/blog with ecommerce capable membership area

We need a WordPress design for FitPennyCoach.com. This is a blog about wellness, weight loss, and health related topics. Design logo will be provided to the winner.

A great site with a design that we would like to emulate are http://qv4.example. The design should be simple, clean, unique, fun, and distinctive. Above all, it should be highly readable and easy to navigate.

These are the specific sections/categories of the blog that should be included and incorporated into the design SEE BELOW.

Thanks in advance for your consideration
Updates

Project Deadline Extended
Reason: I have extended the deadline to evaluate more designs from other pros

Hello all, Please take a minute to review the requirements for this project and please make sure you are capable of meeting ALL the requirements. As you already know I will be making a decision very shortly on whose design I will be moving forward with, if there are any last minute submissions now is the time. Thank you for your time.

Target Market(s)

90 % women 10 % men my clients are usually professionals who value their appearance, health, longevity and time.

Industry/Entity Type

Personal Trainer

Font styles to use
Serif

Colors
886aae
ffcf3e

Requirements
Must have
• Requirements

- start losing weight today.... 555 207 9184 (first line)
- visuals/images and backgrounds to give the idea of wellness, weight loss, healthy living, etc
- navigation menu - home, who we are, what we do, who we serve, blog, contact, members area

1) slider element at top below navigation menu
2) slider element near bottom of page will have testimonials
3) contact form/inquiry form (one page)
4) will provide wellness logo (to give credibility)
5) color scheme purple, gold and white
6) membership area
7) fb, tw, youtube icons
8) footer area - In the footer, there will be smaller company logo, copyright,
disclaimer, privacy policy, terms n conditions, verse of day, and contact info, Phone: (555) 207-9184
Email: support@...
Address:
9) use dummy content/graphic as they will be replaced by real content (the winner will provide instruction on how to make changes to all text and changing graphics)
9) ecommerce enabled / newsletter signup area

```html
<!DOCTYPE html>
<html lang="en">
<head>
<meta charset="utf-8">
<title>FitPennyCoach – Wellness Coaching</title>
<link href="https://fonts.googleapis.com/css2?family=Open+Sans:ital,wght@0,400;0,600;0,700;0,800;1,400&display=swap" rel="stylesheet">
<style>
:root{
  --purple:#7a3a9e;
  --purple-dark:#5e2580;
  --gold:#f2b600;
  --ink:#333;
  --muted:#777;
  --light:#f2f2f2;
  --band:#e6e6e6;
  --footer:#2b2b2b;
  --footer-deep:#1c1c1c;
  --white:#fff;
}
*{box-sizing:border-box;margin:0;padding:0}
html,body{width:1200px;height:2284px;overflow:hidden}
body{font-family:"Open Sans",Arial,sans-serif;color:var(--ink);background:var(--white);font-size:14px;line-height:1.6}
.site-header{height:100px;position:relative;background:var(--white)}
.brand{position:absolute;left:100px;top:32px;display:flex;align-items:center;gap:10px}
.brand-dot{width:14px;height:14px;border-radius:50%;background:var(--ink)}
.brand-name{font-size:24px;font-weight:600;color:var(--ink);line-height:1}
.promo-pill{position:absolute;right:100px;top:0;background:var(--purple);color:var(--white);font-size:14px;font-weight:600;padding:8px 22px 8px 14px;border-radius:0 0 0 20px;display:flex;align-items:center;gap:10px}
.promo-pill .phone-icon{width:22px;height:22px;border-radius:50%;background:var(--white);display:flex;align-items:center;justify-content:center}
.promo-pill .num{color:var(--gold)}
.main-nav{position:absolute;right:100px;top:60px;display:flex;gap:4px}
.main-nav a{font-size:13px;font-weight:600;color:var(--ink);text-decoration:none;padding:6px 12px;text-transform:uppercase}
.main-nav a.active{background:var(--purple);color:var(--white)}
.hero{height:460px;position:relative;background:linear-gradient(100deg,#9a9a9a 0%,#d8d8d8 45%,#efefef 70%,#dcdcdc 100%)}
.hero-photo{position:absolute;inset:0}
.hero-copy{position:absolute;left:640px;top:235px;color:#444}
.hero-copy .line1{font-size:66px;font-weight:400;line-height:1}
.hero-copy .line1 b{color:var(--purple);font-weight:700}
.hero-copy .line2{font-size:42px;font-weight:400;margin-top:6px;padding-left:70px;line-height:1.1}
.hero-dots{position:absolute;left:900px;top:420px;display:flex;gap:8px}
.hero-dots i{width:10px;height:10px;border-radius:50%;background:rgba(255,255,255,.8)}
.hero-dots i.on{background:var(--purple)}
.welcome{height:425px;position:relative;background:var(--white)}
.welcome h1{position:absolute;left:100px;top:40px;font-size:32px;font-weight:600;color:var(--gold);letter-spacing:1px}
.welcome h1 b{color:var(--purple);font-weight:700}
.welcome .rule{position:absolute;left:100px;top:96px;width:700px;height:1px;background:#ddd}
.welcome p{position:absolute;left:100px;top:112px;width:690px;font-size:13.5px;color:var(--muted)}
.checklist{position:absolute;left:100px;top:268px;list-style:none}
.checklist li{display:flex;align-items:center;gap:10px;font-size:13.5px;color:var(--muted);margin-bottom:6px}
.welcome-photo{position:absolute;left:820px;top:20px;width:280px;height:385px;background:linear-gradient(180deg,#f4f4f4,#d9d4de)}
.services{height:420px;position:relative;background:var(--band)}
.arrow{position:absolute;top:190px}
.arrow.left{left:40px}.arrow.right{right:40px}
.service-card{position:absolute;top:55px;width:300px;height:325px;background:var(--white);border:2px solid var(--purple)}
.service-card .icon{position:absolute;left:118px;top:-34px;width:64px;height:64px;border-radius:50%;background:var(--white);border:3px solid var(--purple);display:flex;align-items:center;justify-content:center}
.service-card h2{text-align:center;font-size:26px;font-weight:600;color:var(--purple);margin-top:32px}
.service-card .photo{margin:8px 16px 0;height:200px}
.service-card .btn{position:absolute;left:16px;bottom:-14px;background:var(--purple);color:var(--white);font-size:11px;font-weight:700;padding:5px 16px}
.svc-health{left:100px}.svc-weight{left:450px}.svc-fitness{left:800px}
.cta-band{height:200px;position:relative;background:var(--white)}
.cta-bar{position:absolute;left:100px;top:45px;width:1000px;height:112px;background:linear-gradient(90deg,#111,#3a3a3a);display:flex;align-items:center}
.cta-mark{width:44px;height:44px;background:var(--purple);margin:0 28px 0 34px}
.cta-text{font-size:24px;line-height:1.25;color:var(--white);flex:1}
.cta-btn{border:2px solid var(--white);color:var(--white);font-size:17px;font-weight:600;padding:7px 20px;margin-right:36px;background:var(--purple-dark)}
.testimonials{height:410px;position:relative;background:linear-gradient(180deg,#f7f7f7,#e9e9e9)}
.testimonials h2{text-align:center;font-size:40px;font-weight:700;color:var(--gold);padding-top:20px;letter-spacing:1px}
.quote-badge{position:absolute;left:555px;top:100px;width:90px;height:90px;border-radius:50%;background:var(--purple);display:flex;align-items:center;justify-content:center}
.testimonials blockquote{position:absolute;left:100px;top:220px;width:1000px;text-align:center;font-size:14.5px;color:#444}
.testimonials cite{position:absolute;left:0;right:0;top:338px;text-align:center;font-style:normal;font-size:12px;color:#555;line-height:1.4}
.testimonials cite b{display:block;color:#222}
.site-footer{height:219px;position:relative;background:var(--footer);color:#ccc;font-size:12.5px;line-height:1.55}
.site-footer h3{font-size:15px;font-weight:700;color:var(--white);margin-bottom:8px;text-transform:uppercase}
.f-col{position:absolute;top:24px}
.f-contact{left:100px;width:300px}
.f-resources{left:430px;width:250px}
.f-resources .accent{color:#b78fd6}
.f-form{left:700px;width:400px}
.socials{display:flex;gap:6px;margin-top:4px}
.socials i{width:20px;height:20px;background:var(--purple)}
.field{background:var(--white);height:24px;width:160px;margin-bottom:8px;font-size:11px;color:#999;padding:3px 8px}
.field-msg{position:absolute;left:220px;top:33px;width:180px;height:56px;background:var(--white);font-size:11px;color:#999;padding:3px 8px}
.submit{position:absolute;left:322px;top:122px;background:var(--purple);color:var(--white);font-weight:700;font-size:12px;padding:4px 16px}
.copyright{height:36px;background:var(--footer-deep);color:#aaa;font-size:11px;text-align:center;line-height:36px}
</style>
</head>
<body>

<header class="site-header">
  <div class="brand"><span class="brand-dot"></span><span class="brand-name">FitPennyCoach</span></div>
  <div class="promo-pill">
    <span class="phone-icon"><svg width="12" height="12" viewBox="0 0 24 24"><path fill="#7a3a9e" d="M6.6 10.8a15 15 0 0 0 6.6 6.6l2.2-2.2c.3-.3.7-.4 1-.2 1.1.4 2.3.6 3.6.6.6 0 1 .4 1 1V20c0 .6-.4 1-1 1A17 17 0 0 1 3 4c0-.6.4-1 1-1h3.5c.6 0 1 .4 1 1 0 1.3.2 2.5.6 3.6.1.3 0 .7-.2 1z"/></svg></span>
    Start losing weight today... <span class="num">555 207 9184</span>
  </div>
  <nav class="main-nav">
    <a class="active">Home</a><a>Who we are</a><a>What we do</a><a>Who we serve</a><a>Contact</a><a>Blog</a><a>Members</a>
  </nav>
</header>

<section class="hero">
  <div class="hero-photo" role="img" aria-label="Photo of a smiling couple training with dumbbells in a bright gym"></div>
  <div class="hero-copy">
    <div class="line1">YOUR <b>WELLNESS</b></div>
    <div class="line2">STARTS TODAY</div>
  </div>
  <div class="hero-dots"><i class="on"></i><i></i><i></i><i></i></div>
</section>

<section class="welcome">
  <h1>WELCOME TO <b>WELLNESS</b></h1>
  <div class="rule"></div>
  <p>Lorem ipsum dolor sit amet, consectetur adipiscing elit, sed do eiusmod tempor incididunt ut labore et dolore magna aliqua. Ut enim ad minim veniam, quis nostrud exercitation ullamco laboris nisi ut aliquip ex ea commodo consequat. Duis aute irure dolor in reprehenderit in voluptate velit esse cillum dolore eu fugiat nulla pariatur. Excepteur sint occaecat cupidatat non proident, sunt in culpa qui officia deserunt mollit anim id est laborum. Sed ut perspiciatis unde omnis iste natus error sit voluptatem accusantium doloremque laudantium, totam rem aperiam eaque ipsa quae ab illo inventore veritatis.</p>
  <ul class="checklist">
    <li><svg width="14" height="14" viewBox="0 0 16 16"><path d="M2 8.5l4 4 8-9" fill="none" stroke="#7a3a9e" stroke-width="2.5"/></svg>Contrary to popular belief, lorem ipsum is not simply random text.</li>
    <li><svg width="14" height="14" viewBox="0 0 16 16"><path d="M2 8.5l4 4 8-9" fill="none" stroke="#7a3a9e" stroke-width="2.5"/></svg>Lorem ipsum dolor sit amet, adipiscing elit, nemo enim ipsam.</li>
    <li><svg width="14" height="14" viewBox="0 0 16 16"><path d="M2 8.5l4 4 8-9" fill="none" stroke="#7a3a9e" stroke-width="2.5"/></svg>Sed ut perspiciatis unde omnis iste natus error sit voluptatem.</li>
  </ul>
  <div class="welcome-photo" role="img" aria-label="Photo of a woman eating an apple and holding a bathroom scale"></div>
</section>

<section class="services">
  <svg class="arrow left" width="20" height="36" viewBox="0 0 20 36"><path d="M17 2L3 18l14 16" fill="none" stroke="#555" stroke-width="4"/></svg>
  <svg class="arrow right" width="20" height="36" viewBox="0 0 20 36"><path d="M3 2l14 16L3 34" fill="none" stroke="#555" stroke-width="4"/></svg>

  <article class="service-card svc-health">
    <div class="icon"><svg width="30" height="30" viewBox="0 0 24 24"><path d="M12 21s-8-5.2-8-11a4.5 4.5 0 0 1 8-2.8A4.5 4.5 0 0 1 20 10c0 5.8-8 11-8 11z" fill="#7a3a9e"/></svg></div>
    <h2>Health</h2>
    <div class="photo" role="img" aria-label="Photo of fresh green apples and vegetables" style="background:linear-gradient(135deg,#b9d36a,#6e9a2f)"></div>
    <span class="btn">Read more</span>
  </article>

  <article class="service-card svc-weight">
    <div class="icon"><svg width="30" height="30" viewBox="0 0 24 24"><rect x="3" y="3" width="18" height="18" rx="2" fill="none" stroke="#7a3a9e" stroke-width="2"/><path d="M7 10a5 5 0 0 1 10 0z" fill="#7a3a9e"/></svg></div>
    <h2>Weight Loss</h2>
    <div class="photo" role="img" aria-label="Photo of a woman measuring her waist with a tape measure" style="background:linear-gradient(135deg,#e8c9a9,#b98a66)"></div>
    <span class="btn">Read more</span>
  </article>

  <article class="service-card svc-fitness">
    <div class="icon"><svg width="32" height="32" viewBox="0 0 24 24"><path d="M3 9v6M6 7v10M18 7v10M21 9v6M6 12h12" stroke="#7a3a9e" stroke-width="2.4" fill="none"/></svg></div>
    <h2>Fitness</h2>
    <div class="photo" role="img" aria-label="Photo of a group fitness class stretching in a studio" style="background:linear-gradient(135deg,#f0d9e4,#c99bb3)"></div>
    <span class="btn">Read more</span>
  </article>
</section>

<section class="cta-band">
  <div class="cta-bar">
    <span class="cta-mark"></span>
    <div class="cta-text">Start Feeling and looking better today.<br>Results are typical.</div>
    <span class="cta-btn">Request An Appointment</span>
  </div>
</section>

<section class="testimonials">
  <h2>OUR TESTIMONIALS</h2>
  <div class="quote-badge"><svg width="40" height="32" viewBox="0 0 40 32"><path d="M2 30V18C2 8 7 3 15 2v6c-4 1-6 4-6 8h6v14zM23 30V18c0-10 5-15 13-16v6c-4 1-6 4-6 8h6v14z" fill="#fff"/></svg></div>
  <blockquote>A wonderful serenity has taken possession of my entire soul, like these sweet mornings of spring which I enjoy with my whole heart. I am alone, and feel the charm of existence in this spot, which was created for the bliss of souls like mine. I am so happy, my dear friend, so absorbed in the exquisite sense of mere tranquil existence, that I neglect my talents and feel stronger every day.</blockquote>
  <cite><b>MARA VELL</b>Client, 6 months</cite>
</section>

<footer class="site-footer">
  <div class="f-col f-contact">
    <h3>Contact Us Today</h3>
    Toll Free: (555) 207-9184<br>
    418 Linden Crest Ave, Suite 102<br>
    Palmview, FL 30000<br>
    Local number: 555-207-9185<br>
    Fax number: 555-207-9186<br>
    hello@fitpennycoach.example
  </div>
  <div class="f-col f-resources">
    <h3>Resources</h3>
    Privacy Policy<br>
    <span class="accent">Terms &amp; Conditions</span><br>
    <span class="accent">Disclaimer</span><br>
    <h3 style="margin-top:10px;font-size:13px">Follow us on</h3>
    <div class="socials"><i></i><i></i><i></i></div>
  </div>
  <div class="f-col f-form">
    <h3>Contact Form</h3>
    <div class="field">Name</div>
    <div class="field">Email</div>
    <div class="field">Phone</div>
    <div class="field-msg">Message</div>
    <span class="submit">Submit</span>
  </div>
</footer>
<div class="copyright">Copyright © 2014 FitPennyCoach. All rights reserved.</div>

</body>
</html>
```